Letterhead for Conveyancing Company

Use existing logo to create a letterhead for a conveyancing company. Must be able to be used in Microsoft Word. Easy to read and professional.
Contact information to be at the bottom.
Bright Oak Conveyancing Pty Ltd
ACN 621 984 736PO Box 535 Campbelltown SA 5074
Mobile - 0461739286
Web address - www.brightoakconveyancing.com.au

Requirements
Must have
• Logo and contact details.
• Simple and professional.

```html
<!DOCTYPE html>
<html lang="en">
<head>
<meta charset="utf-8">
<title>Bright Oak Conveyancing – Letterhead</title>
<link href="https://fonts.googleapis.com/css2?family=Roboto:wght@400;500&family=Ubuntu:wght@500&family=Great+Vibes&display=swap" rel="stylesheet">
<style>
  :root{
    --backdrop:#808080;
    --paper:#fafafa;
    --ink:#6d6e71;
    --ink-dark:#58595b;
    --brand-grey:#6d6e71;
    --brand-pink:#e0409a;
    --signature:#1f3a6b;
  }
  *{margin:0;padding:0;box-sizing:border-box}
  html,body{width:1062px;height:1200px;overflow:hidden;background:var(--backdrop)}
  body{font-family:"Roboto",Arial,sans-serif;color:var(--ink);position:relative}
  .letterhead{position:absolute;left:200px;top:132px;width:662px;height:936px;background:var(--paper)}
  .brand-name{position:absolute;top:80px;left:0;width:100%;text-align:center;font-family:"Ubuntu",sans-serif;font-weight:500;font-size:26px;color:var(--brand-grey);letter-spacing:.5px}
  .letter-date{position:absolute;left:41px;top:186px;font-size:10.5px}
  .recipient{position:absolute;left:41px;top:231px;font-size:10.5px;line-height:15px;font-style:normal}
  .recipient strong{font-weight:500;color:var(--ink-dark)}
  .salutation{position:absolute;left:41px;top:321px;font-size:10.5px}
  .letter-body{position:absolute;left:41px;top:351px;width:579px;font-size:10.5px;line-height:15px;text-align:justify;letter-spacing:-.1px}
  .letter-body p{margin-bottom:15px}
  .sign-off{position:absolute;left:41px;top:697px;font-size:10.5px}
  .sign-name{font-weight:500;color:var(--ink-dark)}
  .signature{font-family:"Great Vibes",cursive;font-size:24px;color:var(--signature);margin:4px 0 0 -12px;line-height:26px}
  .sign-role{margin-top:6px}
  .company-footer{position:absolute;left:33px;top:846px;width:595px;text-align:center}
  .company-name{font-family:"Ubuntu",sans-serif;font-weight:500;font-size:14.5px;color:var(--brand-pink);padding-bottom:7px;border-bottom:2px solid var(--brand-pink)}
  .contact-list{display:flex;justify-content:center;gap:9px;margin-top:14px;font-size:10.8px;list-style:none;white-space:nowrap}
  .contact-list li{display:flex;align-items:center;gap:5px}
  .contact-list svg{width:9px;height:9px;fill:var(--brand-pink)}
</style>
</head>
<body>
<main class="letterhead">
  <div class="brand-name">Bright Oak Conveyancing</div>

  <p class="letter-date">30/20/2016</p>

  <address class="recipient">
    <strong>Mr. XYZ Smith</strong><br>
    123, Street No. 123,<br>
    City Name<br>
    Pincode-123456
  </address>

  <p class="salutation">Dear Sir,</p>

  <section class="letter-body">
    <p>Lorem Ipsum is simply dummy text of the printing and typesetting industry. Lorem Ipsum has been the industry's standard dummy text ever since the 1500s, when an unknown printer took a galley of type and scrambled it to make a type specimen book. It has survived not only five centuries, but also the leap into electronic typesetting, remaining essentially unchanged. It was popularised in the 1960s with the release of Lettersheet sheets containing Lorem Ipsum passages, and more recently with desktop publishing software like Folio PageSetter including versions of Lorem Ipsum.</p>
    <p>Lorem Ipsum is simply dummy text of the printing and typesetting industry. Lorem Ipsum has been the industry's standard dummy text ever since the 1500s, when an unknown printer took a galley of type and scrambled it to make a type specimen book. It has survived not only five centuries, but also the leap into electronic typesetting, remaining essentially unchanged. It was popularised in the 1960s with the release of Lettersheet sheets containing Lorem Ipsum passages, and more recently with desktop publishing software like Folio PageSetter including versions of Lorem Ipsum.</p>
    <p>Lorem Ipsum is simply dummy text of the printing and typesetting industry. Lorem Ipsum has been the industry's standard dummy text ever since the 1500s, when an unknown printer took a galley of type and scrambled it to make a type specimen book.</p>
    <p>Lorem Ipsum is simply dummy text of the printing and typesetting industry. Lorem Ipsum has been the industry's standard dummy text ever since the 1500s, when an unknown printer took a galley of type and scrambled it to make a type specimen book.</p>
  </section>

  <div class="sign-off">
    <p class="sign-name">Your Name</p>
    <p class="signature">Your Signature</p>
    <p class="sign-role">CEO &nbsp;|&nbsp; Owner</p>
  </div>

  <footer class="company-footer">
    <p class="company-name">Bright Oak Conveyancing Pty Ltd</p>
    <ul class="contact-list">
      <li><svg viewBox="0 0 10 10"><path d="M1 3.5C1 2 2.5 1.5 5 1.5S9 2 9 3.5V4.5H7V3.5H3V4.5H1Z M2.5 5H7.5L8.5 9H1.5Z"/></svg>0461739286</li>
      <li><svg viewBox="0 0 10 10"><circle cx="5" cy="5" r="4.2" fill="none" stroke="#e0409a" stroke-width="1.2"/><path d="M1 5H9M5 1C3 3 3 7 5 9M5 1C7 3 7 7 5 9" fill="none" stroke="#e0409a" stroke-width="1"/></svg>www.brightoakconveyancing.com.au</li>
      <li><svg viewBox="0 0 10 10"><path d="M5 0.5A3.3 3.3 0 0 1 8.3 3.8C8.3 6.3 5 9.5 5 9.5S1.7 6.3 1.7 3.8A3.3 3.3 0 0 1 5 0.5ZM5 2.5A1.3 1.3 0 1 0 5 5.1A1.3 1.3 0 1 0 5 2.5Z"/></svg>PO Box 871 Marlowdale SA 5096</li>
      <li><svg viewBox="0 0 10 10"><path d="M3 0.5H4.3L4 3H6.2L6.5 0.5H7.8L7.5 3H9.5V4.3H7.3L7 6H9V7.3H6.8L6.5 9.5H5.2L5.5 7.3H3.3L3 9.5H1.7L2 7.3H0.5V6H2.2L2.5 4.3H1V3H2.7ZM3.8 4.3L3.5 6H5.7L6 4.3Z"/></svg>ACN 583 217 469</li>
    </ul>
  </footer>
</main>
</body>
</html>
```